Quill Physical Therapy Website

I would need a clean modern website built to showcase my Physical therapy brand and services. I would need a simple but descriptive website that can ultimately connect my patients to my electronic medical portal so they may book an appointment..

```html
<!DOCTYPE html>
<html lang="en">
<head>
<meta charset="utf-8">
<title>Quill Physical Therapy</title>
<link href="https://fonts.googleapis.com/css2?family=Roboto:ital,wght@0,300;0,400;0,500;0,700;1,400&display=swap" rel="stylesheet">
<style>
:root{
  --teal:#0f8a7e;
  --teal-dark:#0c7a70;
  --green:#7dc24b;
  --ink:#222;
  --muted:#8a8a8a;
  --line:#e3e3e3;
  --light:#f2f2f2;
  --dark:#3b3b3b;
  --white:#fff;
}
*{margin:0;padding:0;box-sizing:border-box}
html,body{width:1200px;height:5027px;overflow:hidden}
body{font-family:'Roboto',Arial,sans-serif;color:var(--ink);background:var(--white);position:relative}
.abs{position:absolute}
.photo{position:absolute}
.btn{position:absolute;display:flex;align-items:center;justify-content:center;border-radius:30px;font-weight:500;text-transform:uppercase}
.btn-green{background:var(--green);color:#fff}
.sec-title{position:absolute;font-size:34px;font-weight:700;text-transform:uppercase;letter-spacing:.3px}
.lorem{font-size:12.5px;line-height:21px;color:var(--muted)}

/* header */
.site-header{position:absolute;left:0;top:0;width:1200px;height:133px;background:#fff;z-index:5}
.topbar{left:315px;top:0;width:769px;height:64px;background:var(--teal);border-radius:0 0 34px 34px;color:#fff;font-size:14px}
.topbar span{position:absolute;top:22px;display:flex;align-items:center;gap:8px;white-space:nowrap}
.topbar .book{right:40px;text-decoration:underline;font-weight:500}
.logo{left:111px;top:4px;width:140px;height:124px}
.logo-mark{position:absolute;left:40px;top:0;width:60px;height:60px;border-radius:50%;background:var(--teal)}
.logo-name{position:absolute;left:0;top:66px;width:140px;text-align:center;font-size:36px;line-height:42px;font-weight:700;color:var(--green)}
.nav{top:94px;font-size:15px;font-weight:500;color:#333;white-space:nowrap}
.nav.active{color:var(--teal)}

/* hero */
.hero{left:0;top:133px;width:1200px;height:734px;background:linear-gradient(100deg,#c9b8a6 0%,#9bb2bf 35%,#dfe2e0 60%,#eef0ee 100%)}
.hero-title{left:599px;top:355px;font-size:56px;line-height:66px;font-weight:500;color:#222}
.hero-text{left:599px;top:500px;width:470px;font-size:16px;line-height:27px;color:#333}
.arrow-box{position:absolute;background:var(--teal);display:flex;align-items:center;justify-content:center}

/* offer */
.card-img{position:absolute;top:1027px;height:217px}
.card-title{position:absolute;top:1262px;font-size:16px;font-weight:500}
.card-text{position:absolute;top:1290px;width:225px}
.sm-btn{top:1366px;height:30px;width:128px;font-size:11.5px}
.ghost-arrow{position:absolute;width:34px;height:34px;border:1px solid #ccc;display:flex;align-items:center;justify-content:center}

/* why */
.why-panel{left:599px;top:1483px;width:601px;height:513px;background:var(--teal);color:#fff}
.stat-num{position:absolute;font-size:38px;font-weight:700}
.stat-lbl{position:absolute;font-size:15px;font-weight:500}

/* advantages */
.adv{position:absolute;width:320px;height:140px;border:1px solid var(--line);background:#fff}
.adv .ic{position:absolute;left:16px;top:42px;width:56px;height:56px;border-radius:50%;border:1px solid var(--line);display:flex;align-items:center;justify-content:center}
.adv .ic.on{background:var(--teal);border-color:var(--teal)}
.adv h4{position:absolute;left:86px;top:40px;font-size:12.5px;font-weight:700;text-transform:uppercase}
.adv p{position:absolute;left:86px;top:62px;width:220px;font-size:11.5px;line-height:20px;color:var(--muted)}

/* doctors */
.doc{position:absolute;top:2627px;width:237px;height:342px;background:var(--light)}
.doc .pic{position:absolute;left:0;top:0;width:237px;height:228px}
.doc h5{position:absolute;top:236px;width:100%;text-align:center;font-size:15px;font-weight:500}
.doc .role{position:absolute;top:259px;width:100%;text-align:center;font-size:12.5px;color:var(--teal)}
.doc .out{position:absolute;left:58px;top:289px;width:122px;height:32px;border:1px solid #bbb;border-radius:18px;display:flex;align-items:center;justify-content:center;font-size:12px;font-weight:500}

/* testimonial */
.testi{left:0;top:3063px;width:1200px;height:362px;background:linear-gradient(90deg,#2f2f2f,#3d3d3d 55%,#55514c)}
.quote{left:200px;top:3243px;width:800px;text-align:center;color:#eee;font-style:italic;font-size:15px;line-height:28px}
.out-arrow{position:absolute;width:47px;height:50px;border:1px solid #ddd;display:flex;align-items:center;justify-content:center}

/* blog */
.blog-img{position:absolute;top:3568px;width:320px;height:256px}
.blog-title{position:absolute;top:3842px;font-size:14px;font-weight:500;text-transform:uppercase}
.blog-text{position:absolute;top:3872px;width:310px}

/* appointment */
.field{position:absolute;left:86px;width:493px;border-bottom:1px solid #ccc;font-size:13px;color:#444}
.appt-box{left:606px;top:4085px;width:404px;height:338px;background:var(--teal);color:#fff}

/* footer */
.footer{left:0;top:4480px;width:1200px;height:547px;background:var(--teal-dark);color:#fff}
.soc{position:absolute;top:4528px;width:40px;height:40px;background:var(--green)}
.f-contact{position:absolute;top:4540px;font-size:13.5px;line-height:18px;color:#fff;white-space:nowrap}
.f-contact b{font-weight:500;display:block}
.f-head{position:absolute;top:4660px;font-size:19px;font-weight:500;color:#fff}
.f-list{position:absolute;top:4705px;font-size:13px;line-height:31px;list-style:none;color:#fff}
.f-list li::before{content:"› ";}
</style>
</head>
<body>

<!-- Header -->
<header class="site-header">
  <div class="abs topbar">
    <span style="left:36px">
      <svg width="14" height="14" viewBox="0 0 24 24"><path fill="#fff" d="M6.6 10.8a15.1 15.1 0 0 0 6.6 6.6l2.2-2.2c.3-.3.7-.4 1-.2 1.1.4 2.3.6 3.6.6.6 0 1 .4 1 1V20c0 .6-.4 1-1 1A17 17 0 0 1 3 4c0-.6.4-1 1-1h3.5c.6 0 1 .4 1 1 0 1.3.2 2.5.6 3.6.1.3 0 .7-.2 1z"/></svg>
      555-014-2200</span>
    <span style="left:160px">
      <svg width="15" height="12" viewBox="0 0 24 18"><rect width="24" height="18" rx="2" fill="#fff"/><path d="M1 2l11 8 11-8" stroke="#0f8a7e" stroke-width="2" fill="none"/></svg>
      info@QuillPhysicalTherapy.com</span>
    <span class="book">Book An Appointment</span>
  </div>
  <div class="abs logo">
    <div class="logo-mark"></div>
    <div class="logo-name">QUILL</div>
  </div>
  <div class="abs nav active" style="left:352px">HOME</div>
  <div class="abs nav" style="left:443px">ABOUT US ▾</div>
  <div class="abs nav" style="left:584px">SERVICES ▾</div>
  <div class="abs nav" style="left:717px">PATIENTS</div>
  <div class="abs nav" style="left:840px">BLOG</div>
  <div class="abs nav" style="left:931px">CONTACT US</div>
  <svg class="abs" style="left:1064px;top:96px" width="16" height="16" viewBox="0 0 24 24"><circle cx="10" cy="10" r="7" stroke="#333" stroke-width="3" fill="none"/><path d="M15 15l7 7" stroke="#333" stroke-width="3"/></svg>
</header>

<!-- Hero -->
<div class="photo hero" role="img" aria-label="Physical therapist stretching a patient's arm and shoulder"></div>
<div class="abs hero-title">QUILL PHYSICAL<br>THERAPY</div>
<div class="abs hero-text">Lorem ipsum dolor sit amet, consectetur adipiscing elit, sed do incididunt ut labore et dolore magna aliqua.</div>
<div class="btn btn-green" style="left:599px;top:582px;width:226px;height:54px;font-size:15px">Get Started</div>
<div class="arrow-box" style="left:0;top:468px;width:52px;height:69px"><svg width="12" height="20" viewBox="0 0 12 20"><path d="M10 2L2 10l8 8" stroke="#fff" stroke-width="2.5" fill="none"/></svg></div>
<div class="arrow-box" style="left:1148px;top:468px;width:52px;height:69px"><svg width="12" height="20" viewBox="0 0 12 20"><path d="M2 2l8 8-8 8" stroke="#fff" stroke-width="2.5" fill="none"/></svg></div>

<!-- What we offer -->
<div class="sec-title" style="left:111px;top:952px">What We Offer</div>
<div class="ghost-arrow" style="left:1000px;top:957px"><svg width="8" height="12"><path d="M7 1L2 6l5 5" stroke="#bbb" stroke-width="1.5" fill="none"/></svg></div>
<div class="ghost-arrow" style="left:1050px;top:957px"><svg width="8" height="12"><path d="M1 1l5 5-5 5" stroke="#444" stroke-width="1.5" fill="none"/></svg></div>

<div class="card-img" style="left:111px;width:237px;background:linear-gradient(135deg,#cfa98f,#8a6d5c)" role="img" aria-label="Chiropractor adjusting a patient's back"></div>
<div class="card-img" style="left:358px;width:237px;background:linear-gradient(135deg,#e7e1d8,#a9a39a)" role="img" aria-label="Physiotherapist guiding an arm exercise"></div>
<div class="card-img" style="left:605px;width:237px;background:linear-gradient(135deg,#c79a7e,#6f4e3e)" role="img" aria-label="Back massage therapy"></div>
<div class="card-img" style="left:852px;width:237px;background:linear-gradient(135deg,#d9d2cf,#5e5a5e)" role="img" aria-label="Cold laser treatment on a leg"></div>

<div class="card-title" style="left:111px">Chiropractic Therapy</div>
<div class="card-title" style="left:358px">Physiotherapy</div>
<div class="card-title" style="left:605px">Massage Therapy</div>
<div class="card-title" style="left:852px">Cold Laser Therapy</div>
<div class="card-text lorem" style="left:111px">Lorem ipsum dolor sit amet, consectetur adipiscing elit, sed do eiusmod incididunt ut labore et dolore magna</div>
<div class="card-text lorem" style="left:358px">Lorem ipsum dolor sit amet, consectetur adipiscing elit, sed do eiusmod incididunt ut labore et dolore magna</div>
<div class="card-text lorem" style="left:605px">Lorem ipsum dolor sit amet, consectetur adipiscing elit, sed do eiusmod incididunt ut labore et dolore magna</div>
<div class="card-text lorem" style="left:852px">Lorem ipsum dolor sit amet, consectetur adipiscing elit, sed do eiusmod incididunt ut labore et dolore magna</div>
<div class="btn btn-green sm-btn" style="left:111px">Read More</div>
<div class="btn btn-green sm-btn" style="left:358px">Read More</div>
<div class="btn btn-green sm-btn" style="left:605px">Read More</div>
<div class="btn btn-green sm-btn" style="left:852px">Read More</div>

<!-- Why choose us -->
<div class="photo" style="left:0;top:1483px;width:599px;height:513px;background:linear-gradient(120deg,#e9e6e2,#c8d2d6 45%,#6b6f73)" role="img" aria-label="Therapist treating a patient's back in a clinic"></div>
<div class="abs why-panel">
  <div class="abs" style="left:30px;top:66px;font-size:33px;font-weight:700;display:flex;align-items:center;gap:12px;white-space:nowrap">WHY CHOOSE US <span style="display:inline-block;width:54px;height:4px;background:#fff"></span></div>
  <p class="abs" style="left:36px;top:130px;width:500px;font-size:13px;line-height:27px">Lorem ipsum dolor sit amet, consectetur adipiscing elit, sed do eiusmod tempor incididunt ut labore et dolore magna aliqua. Ut enim veniam, quis nostrud exercitation ullamco laboris nisi</p>
  <p class="abs" style="left:36px;top:230px;width:500px;font-size:13px;line-height:27px">Lorem ipsum dolor sit amet, consectetur adipiscing elit, sed do eiusmod tempor incididunt ut labore et dolore magna aliqua. Ut enim veniam, quis nostrud exercitation ullamco laboris nisi</p>
  <div class="stat-num" style="left:46px;top:362px">20k</div>
  <div class="stat-lbl" style="left:46px;top:416px">Happy Customers</div>
  <div class="stat-num" style="left:220px;top:362px">3</div>
  <div class="stat-lbl" style="left:220px;top:416px">Years Experience</div>
  <div class="stat-num" style="left:391px;top:362px">100%</div>
  <div class="stat-lbl" style="left:391px;top:416px">Satisfaction</div>
</div>

<!-- Advantages -->
<div class="sec-title" style="left:111px;top:2076px">Our Advantages</div>
<div class="adv" style="left:111px;top:2153px"><div class="ic"><svg width="26" height="26" viewBox="0 0 24 24"><rect x="4" y="4" width="16" height="16" rx="3" stroke="#0f8a7e" stroke-width="1.5" fill="none"/><path d="M12 8v8M8 12h8" stroke="#0f8a7e" stroke-width="1.5"/></svg></div><h4>Personalized Treatment</h4><p>Lorem ipsum dolor sit amet, consectetur adipiscing elit, sed do eiusmod</p></div>
<div class="adv" style="left:439px;top:2153px"><div class="ic on"><svg width="26" height="26" viewBox="0 0 24 24"><path d="M5 12l5 5 9-10" stroke="#fff" stroke-width="2.5" fill="none"/></svg></div><h4>Licensed Therapists</h4><p>Lorem ipsum dolor sit amet, consectetur adipiscing elit, sed do eiusmod</p></div>
<div class="adv" style="left:769px;top:2153px"><div class="ic"><svg width="26" height="26" viewBox="0 0 24 24"><path d="M2 9l10-4 10 4-10 4z M6 11v5c3 2 9 2 12 0v-5" stroke="#0f8a7e" stroke-width="1.5" fill="none"/></svg></div><h4>Experience Staff</h4><p>Lorem ipsum dolor sit amet, consectetur adipiscing elit, sed do eiusmod</p></div>
<div class="adv" style="left:111px;top:2304px"><div class="ic"><svg width="26" height="26" viewBox="0 0 24 24"><path d="M4 21V8h16v13M8 12h2M14 12h2M8 16h2M14 16h2M10 21v-3h4v3M12 3v3M10.5 4.5h3" stroke="#0f8a7e" stroke-width="1.5" fill="none"/></svg></div><h4>Comfortable Clinic</h4><p>Lorem ipsum dolor sit amet, consectetur adipiscing elit, sed do eiusmod</p></div>
<div class="adv" style="left:439px;top:2304px"><div class="ic"><svg width="26" height="26" viewBox="0 0 24 24"><circle cx="8" cy="8" r="3" stroke="#0f8a7e" stroke-width="1.5" fill="none"/><circle cx="16" cy="8" r="3" stroke="#0f8a7e" stroke-width="1.5" fill="none"/><path d="M3 19c0-4 10-4 10 0M11 19c0-4 10-4 10 0" stroke="#0f8a7e" stroke-width="1.5" fill="none"/></svg></div><h4>Practitioners Network</h4><p>Lorem ipsum dolor sit amet, consectetur adipiscing elit, sed do eiusmod</p></div>
<div class="adv" style="left:769px;top:2304px"><div class="ic"><svg width="26" height="26" viewBox="0 0 24 24"><circle cx="12" cy="12" r="8" stroke="#0f8a7e" stroke-width="1.5" fill="none"/><circle cx="12" cy="12" r="3" stroke="#0f8a7e" stroke-width="1.5" fill="none"/></svg></div><h4>Therapy Goals</h4><p>Lorem ipsum dolor sit amet, consectetur adipiscing elit, sed do eiusmod</p></div>

<!-- Doctors -->
<div class="abs" style="left:0;top:2520px;width:1200px;text-align:center;font-size:34px;font-weight:700">MEET OUR DOCTORS</div>
<div class="abs" style="left:0;top:2577px;width:1200px;text-align:center;font-size:15px;color:var(--teal)">This is our medical physiotherapy team</div>
<div class="doc" style="left:111px"><div class="pic" style="background:linear-gradient(160deg,#e8e4df,#b9b2aa)" role="img" aria-label="Therapist seated beside a treatment table"></div><h5>JOHN DOE</h5><div class="role">Therapist</div><div class="out">READ MORE</div></div>
<div class="doc" style="left:358px"><div class="pic" style="background:linear-gradient(160deg,#ece8e2,#c2b7aa)" role="img" aria-label="Therapist holding a clipboard"></div><h5>JOHN DOE</h5><div class="role">Therapist</div><div class="out">READ MORE</div></div>
<div class="doc" style="left:605px"><div class="pic" style="background:linear-gradient(160deg,#6d6f6e,#3e4c46)" role="img" aria-label="Doctor in green scrubs"></div>
  <div class="abs" style="left:45px;top:96px;width:44px;height:40px;background:var(--green)"></div>
  <div class="abs" style="left:97px;top:96px;width:44px;height:40px;background:var(--green)"></div>
  <div class="abs" style="left:149px;top:96px;width:44px;height:40px;background:var(--green)"></div>
  <h5>JOHN DOE</h5><div class="role">Doctor</div><div class="out">READ MORE</div></div>
<div class="doc" style="left:852px"><div class="pic" style="background:linear-gradient(160deg,#eeebe6,#bdb6ad)" role="img" aria-label="Therapist standing with arms crossed"></div><h5>JOHN DOE</h5><div class="role">Therapist</div><div class="out">READ MORE</div></div>

<!-- Testimonial -->
<div class="photo testi" role="img" aria-label="Dimmed background of a therapy session"></div>
<div class="photo" style="left:549px;top:3121px;width:100px;height:100px;border-radius:50%;border:3px solid #fff;background:linear-gradient(160deg,#d6cfc6,#9c9189)" role="img" aria-label="Reviewer portrait"></div>
<div class="abs quote">Lorem ipsum dolor sit amet, consectetur adipiscing elit, sed do eiusmod tempor incididunt ut labore et dolore magna aliqua. Ut enim ad minim veniam, quis nostrud exercitation ullamco laboris nisi ut aliquip ex ea commodo consequat. Duis aute irure dolor in reprehendert</div>
<div class="abs" style="left:0;top:3345px;width:1200px;text-align:center;color:#fff;font-size:16px">Mara Ellison</div>
<div class="out-arrow" style="left:133px;top:3252px"><svg width="10" height="16"><path d="M8 2L2 8l6 6" stroke="#fff" stroke-width="2" fill="none"/></svg></div>
<div class="out-arrow" style="left:1015px;top:3252px"><svg width="10" height="16"><path d="M2 2l6 6-6 6" stroke="#fff" stroke-width="2" fill="none"/></svg></div>

<!-- Blogs -->
<div class="abs" style="left:0;top:3497px;width:1200px;text-align:center;font-size:34px;font-weight:700">LATEST BLOGS</div>
<div class="blog-img" style="left:111px;background:linear-gradient(140deg,#e4ddd4,#a8b39d)" role="img" aria-label="Therapist treating a patient lying on a table"></div>
<div class="blog-img" style="left:439px;background:linear-gradient(140deg,#55585b,#b9b6b2)" role="img" aria-label="Person holding a sore knee"></div>
<div class="blog-img" style="left:769px;background:linear-gradient(140deg,#ece7e4,#c9a6a1)" role="img" aria-label="Therapist assisting a floor exercise"></div>
<div class="blog-title" style="left:111px">Lorem ipsum dolor sit amet</div>
<div class="blog-title" style="left:439px">Lorem ipsum dolor sit amet</div>
<div class="blog-title" style="left:769px">Lorem ipsum dolor sit amet</div>
<div class="blog-text lorem" style="left:111px">Sed ut perspiciatis unde omnis iste natus error sit voluptatem accusantium laudantium, totam rem aperiam, eaque ipsa quae ab illo inventore</div>
<div class="blog-text lorem" style="left:439px">Sed ut perspiciatis unde omnis iste natus error sit voluptatem accusantium laudantium, totam rem aperiam, eaque ipsa quae ab illo inventore</div>
<div class="blog-text lorem" style="left:769px">Sed ut perspiciatis unde omnis iste natus error sit voluptatem accusantium laudantium, totam rem aperiam, eaque ipsa quae ab illo inventore</div>

<!-- Appointment -->
<div class="abs" style="left:0;top:4029px;width:1200px;height:451px;background:#fafafa"></div>
<div class="photo" style="left:936px;top:4029px;width:264px;height:451px;background:linear-gradient(170deg,#dfe6ea,#9ab4c4)" role="img" aria-label="Therapist stretching a patient's arm"></div>
<div class="field" style="top:4082px;height:30px">Name</div>
<div class="field" style="top:4141px;height:30px">Email Address</div>
<div class="field" style="top:4200px;height:30px">Phone Number</div>
<div class="field" style="top:4259px;height:72px">Message</div>
<div class="btn btn-green" style="left:86px;top:4361px;width:224px;height:60px;font-size:16px">Submit</div>
<div class="abs appt-box">
  <div class="abs" style="left:34px;top:32px;font-size:25px;font-weight:700;white-space:nowrap">GET APPOINTMENT</div>
  <div class="abs" style="left:38px;top:80px;width:330px;font-size:17px;line-height:33px;font-weight:500;color:#e9f5e0">YOU CAN DROP MESSAGE FOR ANY QUERRY.</div>
  <div class="abs" style="left:38px;top:165px;width:72px;height:4px;background:#fff"></div>
  <div class="abs" style="left:38px;top:222px;font-size:15px;font-weight:500">CALL US ON</div>
  <div class="abs" style="left:38px;top:252px;font-size:37px;font-weight:700;white-space:nowrap">555-014-2200</div>
</div>

<!-- Footer -->
<div class="abs footer"></div>
<div class="soc" style="left:111px"></div>
<div class="soc" style="left:163px"></div>
<div class="soc" style="left:215px"></div>
<div class="soc" style="left:267px"></div>

<svg class="abs" style="left:405px;top:4532px" width="28" height="40" viewBox="0 0 24 34"><path d="M12 0a12 12 0 0 0-12 12c0 9 12 22 12 22s12-13 12-22A12 12 0 0 0 12 0z" fill="#7dc24b"/><circle cx="12" cy="12" r="5" fill="#0c7a70"/></svg>
<div class="f-contact" style="left:450px"><b>Visit our Location</b>418 Linden Avenue, USA</div>
<svg class="abs" style="left:626px;top:4533px" width="38" height="38" viewBox="0 0 24 24"><path fill="#7dc24b" d="M6.6 10.8a15.1 15.1 0 0 0 6.6 6.6l2.2-2.2c.3-.3.7-.4 1-.2 1.1.4 2.3.6 3.6.6.6 0 1 .4 1 1V20c0 .6-.4 1-1 1A17 17 0 0 1 3 4c0-.6.4-1 1-1h3.5c.6 0 1 .4 1 1 0 1.3.2 2.5.6 3.6.1.3 0 .7-.2 1z"/></svg>
<div class="f-contact" style="left:680px"><b>Give us a Call</b>555-014-2200</div>
<svg class="abs" style="left:828px;top:4540px" width="40" height="28" viewBox="0 0 40 28"><rect width="40" height="28" fill="#7dc24b"/><path d="M1 1l19 14L39 1" stroke="#0c7a70" stroke-width="2.5" fill="none"/></svg>
<div class="f-contact" style="left:886px"><b>Send us a Message</b>info@QuillPhysicalTherapy.com</div>

<div class="f-head" style="left:111px">About Us</div>
<p class="abs" style="left:111px;top:4703px;width:300px;font-size:13px;line-height:27px;color:#fff">Lorem ipsum dolor sit amet, consectetur adipiscing elit, sed do eiusmod tempor incididunt ut labore et dolore magna aliqua. Ut enim ad minim veniam, quis nostrud exercitatio</p>
<div class="f-head" style="left:488px">Navigation</div>
<ul class="f-list" style="left:488px"><li>Home</li><li>About Us</li><li>Services</li><li>Patients</li><li>Blog</li><li>Contact Us</li></ul>
<div class="f-head" style="left:665px">Our Services</div>
<ul class="f-list" style="left:665px"><li>Chiropractic Therapy</li><li>Clinical Pilates</li><li>Massage Therapy</li><li>Physical Therapy</li><li>Sport Injuries</li><li>Work Injuries</li></ul>
<div class="f-head" style="left:875px">Opening Hours</div>
<div class="abs" style="left:875px;top:4705px;font-size:13px;line-height:31px;color:#fff">Mon - Fri<br>Saturday<br>Sunday</div>
<div class="abs" style="left:990px;top:4705px;font-size:13px;line-height:31px;color:#fff">9:00am - 5:30pm<br>9:00am - 3:30pm<br>CLOSED</div>
<div class="abs" style="left:0;top:4923px;width:1200px;height:1px;background:rgba(255,255,255,.15)"></div>
<div class="abs" style="left:0;top:4972px;width:1200px;text-align:center;font-size:14px;color:#fff">© 2021 All Rights Reserved</div>

</body>
</html>
```